Support Welcome Packet Redesign

Looking to redesign our current "welcome packet" that we send to our new customers to help them understand our support service. It is currently in Microsoft Word and would like to remain in either word or publisher. Something that we can easily edit, as the content adjusts based on the customer needs. We want this document to be simple and understandable as it should be something our customers can reference at any time during our contract and easy to navigate.

Target Market(s)

Current Customers. Healthcare, Oil & Gas, Transportation, etc.

Industry/Entity Type

It Service

Font styles to use
Sans Serif

Requirements
Must have
• Table of Contents, inVex Logo and current content
Nice to have
• Easy navigation. Redone final page (contact info)

```html
<!DOCTYPE html>
<html lang="en">
<head>
<meta charset="utf-8">
<title>Services Summary – inVex Welcome Packet</title>
<link href="https://fonts.googleapis.com/css2?family=Carlito:wght@400;700&display=swap" rel="stylesheet">
<style>
  :root{
    --sun-yellow:#fdc21e;
    --accent-orange:#f0a81c;
    --line-orange:#f5b324;
    --ink:#1f1f1f;
    --muted:#5c5c5c;
    --link:#6b6b6b;
    --cloud:#fff6cf;
    --cloud-edge:#f7c230;
    --brand-blue:#2f8fd0;
    --brand-green:#6aa84f;
    --brand-red:#e2583e;
  }
  *{margin:0;padding:0;box-sizing:border-box}
  html,body{width:848px;height:1200px;overflow:hidden;background:#fff}
  body{font-family:"Carlito","Calibri",Arial,sans-serif;color:var(--ink)}
  .page{position:relative;width:848px;height:1200px;overflow:hidden;
    background:linear-gradient(180deg,#e4e4e4 0px,#f3f3f3 260px,#ffffff 560px,#ffffff 1200px)}
  .header-art{position:absolute;left:0;top:0;width:848px;height:270px}
  .page-title{position:absolute;left:80px;top:52px;color:#fff;font-size:32px;font-weight:700}
  .brand-tile{position:absolute;left:690px;top:0;width:116px;height:184px;background:#fff;
    display:flex;flex-direction:column;align-items:center;justify-content:center;gap:10px}
  .brand-tile .mark{width:22px;height:22px;background:var(--muted)}
  .brand-tile .name{font-size:30px;font-weight:400;color:var(--muted)}
  .content{position:absolute;left:80px;top:296px;width:708px}
  .section-heading{color:var(--accent-orange);font-size:26px;font-weight:700;margin-bottom:14px}
  .intro{font-size:20px;line-height:28px}
  .intro a{color:var(--link);font-weight:700}
  .service-list{list-style:none;margin-top:26px}
  .service-list li{position:relative;padding-left:52px;font-size:20px;line-height:28px;margin-bottom:14px;text-align:justify}
  .service-list li::before{content:"";position:absolute;left:23px;top:11px;width:7px;height:7px;border-radius:50%;background:var(--ink)}
  .service-list li.wide{text-align-last:justify}
  .service-list li.wide span{display:block;text-align-last:left}
  .trailing-note{font-size:20px;line-height:28px;margin-top:-2px}
  .footer{position:absolute;left:52px;top:1064px;width:744px;height:30px;display:flex;align-items:center;font-size:15px}
  .footer .brand{display:flex;align-items:center;gap:8px;font-size:20px;font-weight:700;color:var(--muted);margin-right:20px}
  .footer .brand i{width:16px;height:16px;background:var(--muted);display:block}
  .footer .item{display:flex;align-items:center;gap:5px;margin-right:18px}
  .rule{position:absolute;left:8px;top:1098px;width:840px;height:6px;
    background:linear-gradient(90deg,#3d9ad6 0%,#8fc6ea 22%,#f1f1f1 30%,#f19a3e 45%,#e86b2b 55%,#f7d23a 65%,#fbe36b 73%,#9bc45a 86%,#5f9e3a 100%)}
  .page-number{position:absolute;right:62px;top:1114px;font-size:20px}
</style>
</head>
<body>
<main class="page">
  <svg class="header-art" viewBox="0 0 848 270" aria-hidden="false">
    <path d="M0 0 H492 L560 60 Q590 95 520 112 L0 118 Z" fill="var(--sun-yellow)"/>
    <path d="M492 0 L700 208 Q720 232 760 236 L848 236" fill="none" stroke="var(--line-orange)" stroke-width="4"/>
    <g role="img" aria-label="Illustration of a rising sun with rays">
      <ellipse cx="505" cy="132" rx="85" ry="50" fill="var(--sun-yellow)" opacity="0.85"/>
    </g>
    <g role="img" aria-label="Illustration of two small clouds">
      <rect x="70" y="150" width="128" height="52" rx="26" fill="var(--cloud)" stroke="var(--cloud-edge)" stroke-width="2"/>
      <rect x="256" y="128" width="122" height="50" rx="25" fill="var(--cloud)" stroke="var(--cloud-edge)" stroke-width="2"/>
    </g>
  </svg>
  <h1 class="page-title">Services Summary</h1>
  <div class="brand-tile"><span class="mark"></span><span class="name">inVex</span></div>

  <section class="content">
    <h2 class="section-heading">Services Summary</h2>
    <p class="intro">The summary of services that <strong>inVex</strong> is supporting are listed below.&nbsp; Our goal is to assist you in clearly understanding these services.&nbsp; For information on how to use your services, please go to <a href="#">https://invex.supportdesk.net/hc/en-us</a> or feel free to contact us directly for additional support.</p>
    <ul class="service-list">
      <li>Hosted Mailhub</li>
      <li>Hosted Linkwave</li>
      <li>Hosted Servers</li>
      <li>Hosted email security with Shieldwise Antivirus</li>
      <li>Server Backups</li>
      <li>Q4 Service Management System</li>
      <li>Hosted TeamVault</li>
      <li class="wide">Assisted in terminal server configuration (supported during <span>implementation – not a managed service)</span></li>
    </ul>
    <p class="trailing-note">Netara Configuration (supported during implementation – not a managed service)</p>
  </section>

  <footer class="footer">
    <div class="brand"><i></i>inVex Technology</div>
    <div class="item"><svg width="14" height="18" viewBox="0 0 14 18"><path d="M7 0a7 7 0 0 0-7 7c0 5 7 11 7 11s7-6 7-11a7 7 0 0 0-7-7zm0 10a3 3 0 1 1 0-6 3 3 0 0 1 0 6z" fill="var(--brand-blue)"/></svg>420 W Cedar Ave&nbsp; Mesa, AZ 85201</div>
    <div class="item"><svg width="14" height="16" viewBox="0 0 14 16"><path d="M3 0l3 4-2 2c1 2 3 4 5 5l2-2 3 3-2 3C6 15 0 8 0 3z" fill="var(--brand-blue)"/></svg>480-555-0192</div>
    <div class="item"><svg width="16" height="16" viewBox="0 0 16 16"><circle cx="8" cy="8" r="7.5" fill="var(--brand-blue)"/><path d="M2 6c3 0 4 2 6 1s2-4 5-3M4 12c2-2 5-1 7 0" stroke="#fff" stroke-width="1.4" fill="none"/></svg>www.INVEXCORP.com</div>
  </footer>
  <div class="rule"></div>
  <div class="page-number">4</div>
</main>
</body>
</html>
```